BrivoTerna. Lantern of the Steady Harvest. Business card

Professional business card for BrivoTerna (Lantern of the Steady Harvest)
My rationale: Strategy-> Execution-> Results-> Value that lead to the BrivoTerna name: We put the Lantern of the Steady Harvest.
We deliver value to our customers helping them at defining a good strategy (cyan arrow). 90% of well formulated strategies fail due to poor execution so we also consider strategical execution very important (green arrow). Due to the execution we obtain the results (blue arrow). Finally, the results provide feedback to redefine strategy, and the new strategy has to be executed and new results obtained providing new feedback and on and on. It's like a wheel that finally, must create corporate value: value for shareholders, staholders, employees, providers...-

Target Market(s)

CEOs and steering comitees , invewrnent funds

Industry/Entity Type

Business Consultant

Contact Information for Business Card

Teodoro Vinsquel
CEO & Founder
teodoro.vinsquel@brivoterna-example.com
Mobile: +34 655.803.912
www.brivoterna-example.com

Colors

Designer to choose colors to be used in the design.

Requirements
Nice to have
• Nice to hace the words: Strategy, execution, results
• Nice to vave the claim: Lantern of the Steady Harvest
• The three colors should be shown:
• cyan for STRATEGY
• green for EXECUTION
• blue for RESULTS
Should not have
• Complete black background

```html
<!DOCTYPE html>
<html lang="en">
<head>
<meta charset="utf-8">
<title>BrivoTerna Business Card</title>
<link rel="stylesheet" href="https://fonts.googleapis.com/css2?family=Open+Sans:wght@400;600;700&display=swap">
<style>
  :root {
    --page: #e6e8ec;
    --card: #fbfbfc;
    --blue: #0a3296;
    --cyan: #16a9e6;
    --green: #8cc63f;
    --ink: #3a3a3a;
    --rule: #c9ccd2;
  }
  * { box-sizing: border-box; margin: 0; padding: 0; }
  html, body { width: 1200px; height: 900px; overflow: hidden; }
  body {
    background: var(--page);
    font-family: "Open Sans", Arial, sans-serif;
    position: relative;
  }
  .card {
    position: absolute;
    width: 660px;
    height: 380px;
    left: 270px;
    background: var(--card);
    border-radius: 22px;
    overflow: hidden;
    box-shadow: 0 8px 24px rgba(20, 30, 60, 0.18);
  }
  .card-front { top: 40px; }
  .card-back { top: 470px; }
  .card svg.art { position: absolute; inset: 0; }

  .brand {
    position: absolute;
    display: flex;
    align-items: center;
    gap: 12px;
    color: var(--blue);
    font-weight: 700;
    letter-spacing: -0.5px;
  }
  .brand-dot {
    background: var(--blue);
    border-radius: 50%;
  }
  .card-front .brand { left: 40px; top: 150px; font-size: 42px; }
  .card-front .brand-dot { width: 20px; height: 20px; }

  .divider {
    position: absolute;
    left: 318px; top: 48px;
    width: 1px; height: 150px;
    background: var(--rule);
  }
  .contact {
    position: absolute;
    left: 340px; top: 50px;
    color: var(--ink);
  }
  .contact-name {
    color: var(--blue);
    font-weight: 700;
    font-size: 21px;
    line-height: 1.2;
  }
  .contact-title { font-size: 15px; margin-bottom: 14px; }
  .contact-list { list-style: none; font-size: 13.5px; }
  .contact-list li { display: flex; align-items: center; gap: 8px; line-height: 22px; }
  .contact-list svg { width: 13px; height: 13px; flex: none; }

  .card-back .brand { left: 0; right: 0; justify-content: center; top: 120px; font-size: 62px; }
  .card-back .brand-dot { width: 28px; height: 28px; }
  .tagline {
    position: absolute;
    left: 0; right: 0; top: 292px;
    text-align: center;
    color: var(--cyan);
    font-weight: 700;
    font-size: 22px;
    letter-spacing: 2px;
  }
</style>
</head>
<body>

<section class="card card-front">
  <svg class="art" viewBox="0 0 660 380" aria-hidden="true">
    <path d="M0 318 C 220 318, 470 270, 660 170 L660 380 L0 380 Z" fill="var(--blue)"/>
    <path d="M0 306 C 220 306, 470 256, 660 152 L660 160 C 470 264, 220 314, 0 314 Z" fill="var(--green)"/>
    <path d="M240 294 C 400 284, 540 240, 660 140 L660 146 C 540 248, 400 292, 240 300 Z" fill="var(--cyan)"/>
  </svg>

  <div class="brand"><span class="brand-dot"></span>BrivoTerna</div>
  <div class="divider"></div>

  <div class="contact">
    <p class="contact-name">Teodoro Vinsquel</p>
    <p class="contact-title">CEO &amp; Founder</p>
    <ul class="contact-list">
      <li>
        <svg viewBox="0 0 16 16"><path d="M4 1 L6.5 4 L5 6 C6 8.5 7.5 10 10 11 L12 9.5 L15 12 L13 15 C7 14.5 1.5 9 1 3 Z" fill="var(--blue)"/></svg>
        +34 655.803.912
      </li>
      <li>
        <svg viewBox="0 0 16 16"><rect x="1" y="3" width="14" height="10" rx="1" fill="var(--blue)"/><path d="M1.5 3.5 L8 9 L14.5 3.5" stroke="#fff" stroke-width="1.3" fill="none"/></svg>
        teodoro.vinsquel@brivoterna-example.com
      </li>
      <li>
        <svg viewBox="0 0 16 16"><circle cx="8" cy="8" r="7" fill="var(--blue)"/><path d="M1 8 H15 M8 1 C5 4 5 12 8 15 M8 1 C11 4 11 12 8 15" stroke="#fff" stroke-width="1" fill="none"/></svg>
        www.brivoterna-example.com
      </li>
    </ul>
  </div>
</section>

<section class="card card-back">
  <svg class="art" viewBox="0 0 660 380" aria-hidden="true">
    <rect x="0" y="264" width="660" height="4" fill="var(--green)"/>
    <rect x="0" y="270" width="660" height="64" fill="var(--blue)"/>
  </svg>
  <div class="brand"><span class="brand-dot"></span>BrivoTerna</div>
  <p class="tagline">RESULTS • EXECUTION • STRATEGY</p>
</section>

</body>
</html>
```